Business Card Design

Electronic Security Installation Specialists

Check out our website at www.tallbrookllc.com to see what we do.

Industry/Entity Type

Business

Contact Information for Business Card

Tall Brook
Marjorie Hadley
281 Orchard Rise
Mapleton, WV 25871

Colors
3176b5
0455a3
ffffff

```html
<!DOCTYPE html>
<html lang="en">
<head>
<meta charset="utf-8">
<title>Tall Brook – Business Card</title>
<link rel="stylesheet" href="https://fonts.googleapis.com/css2?family=Jura:wght@500;600;700&display=swap">
<style>
  :root {
    --brand-blue: #0455a3;
    --brand-blue-light: #3176b5;
    --paper: #ffffff;
    --paper-shade: #eceef1;
    --rule-grey: #9a9da3;
    --ink: #2b2d31;
    --backdrop: #e4e7ee;
  }
  * { margin: 0; padding: 0; box-sizing: border-box; }
  html, body {
    width: 1200px;
    height: 840px;
    overflow: hidden;
    background: var(--backdrop);
    font-family: "Jura", sans-serif;
  }
  .canvas {
    position: relative;
    width: 1200px;
    height: 840px;
  }
  .business-card {
    position: absolute;
    left: 80px;
    top: 120px;
    width: 1040px;
    height: 600px;
    background: radial-gradient(ellipse at 60% 55%, var(--paper) 0%, var(--paper-shade) 100%);
    box-shadow: 0 10px 30px rgba(30, 40, 70, 0.18);
    overflow: hidden;
  }
  .card-artwork {
    position: absolute;
    inset: 0;
    width: 100%;
    height: 100%;
  }
  .holder-identity {
    position: absolute;
    top: 36px;
    right: 44px;
    text-align: right;
    color: var(--paper);
  }
  .holder-name {
    font-size: 40px;
    font-weight: 700;
    letter-spacing: 2px;
    text-transform: uppercase;
    line-height: 1.1;
  }
  .holder-title {
    font-size: 26px;
    font-weight: 600;
    letter-spacing: 1px;
    margin-top: 2px;
  }
  .brand-mark {
    position: absolute;
    left: 240px;
    top: 262px;
    display: flex;
    align-items: center;
    gap: 16px;
  }
  .brand-dot {
    width: 80px;
    height: 80px;
    border-radius: 50%;
    background: var(--brand-blue);
  }
  .brand-name {
    font-size: 36px;
    font-weight: 700;
    color: var(--brand-blue);
    letter-spacing: 1px;
  }
  .office-address {
    position: absolute;
    right: 44px;
    top: 372px;
    text-align: right;
    font-style: normal;
    font-size: 26px;
    font-weight: 600;
    color: var(--ink);
    line-height: 1.3;
    letter-spacing: 1px;
  }
  .contact-list {
    position: absolute;
    left: 40px;
    top: 412px;
    list-style: none;
    font-size: 22px;
    font-weight: 600;
    color: var(--ink);
    letter-spacing: 1px;
  }
  .contact-item {
    display: flex;
    align-items: center;
    gap: 12px;
    height: 34px;
  }
  .contact-icon {
    width: 20px;
    height: 20px;
    flex: none;
    fill: var(--ink);
  }
</style>
</head>
<body>
<main class="canvas">
  <article class="business-card">
    <svg class="card-artwork" viewBox="0 0 1040 600" preserveAspectRatio="none" aria-hidden="true">
      <defs>
        <linearGradient id="band-fill" x1="0" y1="0" x2="1" y2="0">
          <stop offset="0" stop-color="var(--brand-blue)"/>
          <stop offset="1" stop-color="var(--brand-blue-light)"/>
        </linearGradient>
      </defs>
      <path class="header-band" fill="url(#band-fill)"
            d="M0,0 H1040 V140 C820,170 560,160 380,190 C210,220 70,300 0,380 Z"/>
      <path class="band-rule" fill="none" stroke="var(--rule-grey)" stroke-width="4"
            d="M0,400 C70,320 210,240 380,210 C560,180 820,190 1040,160"/>
    </svg>

    <header class="holder-identity">
      <h1 class="holder-name">Marjorie Hadley</h1>
      <p class="holder-title">Managing Director</p>
    </header>

    <div class="brand-mark">
      <span class="brand-dot"></span>
      <span class="brand-name">Tall Brook</span>
    </div>

    <address class="office-address">
      281 Orchard Rise<br>
      Mapleton, WV 25871
    </address>

    <ul class="contact-list">
      <li class="contact-item">
        <svg class="contact-icon" viewBox="0 0 24 24"><path d="M6.6 10.8a15.1 15.1 0 0 0 6.6 6.6l2.2-2.2a1 1 0 0 1 1-.25 11.4 11.4 0 0 0 3.6.57 1 1 0 0 1 1 1V20a1 1 0 0 1-1 1A17 17 0 0 1 3 4a1 1 0 0 1 1-1h3.5a1 1 0 0 1 1 1c0 1.25.2 2.450.57 3.57a1 1 0 0 1-.25 1Z"/></svg>
        <span>304 555 0142</span>
      </li>
      <li class="contact-item">
        <svg class="contact-icon" viewBox="0 0 24 24"><path d="M7 1h10a2 2 0 0 1 2 2v18a2 2 0 0 1-2 2H7a2 2 0 0 1-2-2V3a2 2 0 0 1 2-2Zm0 3v14h10V4Zm5 15.5a1 1 0 1 0 0 2 1 1 0 0 0 0-2Z"/></svg>
        <span>304 555 0187</span>
      </li>
      <li class="contact-item">
        <svg class="contact-icon" viewBox="0 0 24 24"><path d="M6 2h9l3 3v5H6Zm-3 9h18a1 1 0 0 1 1 1v9a1 1 0 0 1-1 1H3a1 1 0 0 1-1-1v-9a1 1 0 0 1 1-1Zm4 3v2h3v-2Zm5 0v2h3v-2Zm-5 3v2h3v-2Zm5 0v2h3v-2Z"/></svg>
        <span>304 555 0193</span>
      </li>
      <li class="contact-item">
        <svg class="contact-icon" viewBox="0 0 24 24"><path d="M2 5h20v14H2Zm2 2v.5l8 5.5 8-5.5V7l-8 5.5Z"/></svg>
        <span>info@tallbrookllc.com</span>
      </li>
      <li class="contact-item">
        <svg class="contact-icon" viewBox="0 0 24 24"><path d="M12 2a10 10 0 1 0 0 20 10 10 0 0 0 0-20Zm6.9 6h-3a15 15 0 0 0-1.3-3.8A8 8 0 0 1 18.9 8ZM12 4c.9 1.2 1.6 2.6 2 4h-4c.4-1.4 1.1-2.8 2-4ZM4.3 14a8 8 0 0 1 0-4h3.4a16 16 0 0 0 0 4Zm.8 2h3a15 15 0 0 0 1.3 3.8A8 8 0 0 1 5.1 16Zm3-8h-3a8 8 0 0 1 4.3-3.8A15 15 0 0 0 8.1 8ZM12 20c-.9-1.2-1.6-2.6-2-4h4c-.4 1.4-1.1 2.8-2 4Zm2.3-6H9.7a14 14 0 0 1 0-4h4.6a14 14 0 0 1 0 4Zm.3 5.8a15 15 0 0 0 1.3-3.8h3a8 8 0 0 1-4.3 3.8Zm1.7-5.8a16 16 0 0 0 0-4h3.4a8 8 0 0 1 0 4Z"/></svg>
        <span>www.tallbrookllc.com</span>
      </li>
    </ul>
  </article>
</main>
</body>
</html>
```